Local Roofing/Construction company business needs new biz card design

We need a new business card design, current cards are from the start of this operation and generic at best. We are a local Construction Company (General Contractor) with a majority of our work originating from insurance claims-exterior finish work is the main focus (Roofs-Siding-Gutters etc). Heavily involved with homeowners and the low ball offers they receive from insurance company's after a insurable event takes place. I have attached some of our original logo file(s) below.

```html
<!DOCTYPE html>
<html lang="en">
<head>
<meta charset="utf-8">
<title>Halvorsen Construction – Business Card</title>
<link rel="stylesheet" href="https://fonts.googleapis.com/css2?family=Montserrat:wght@400;500;700;800&display=swap">
<style>
  :root {
    --bg: #2a2a2c;
    --card: #1e1e1f;
    --green: #2ed47a;
    --white: #f4f4f4;
    --muted: #d8d8d8;
  }
  * { margin: 0; padding: 0; box-sizing: border-box; }
  html, body { width: 1200px; height: 900px; overflow: hidden; }
  body {
    background: var(--bg);
    font-family: "Montserrat", sans-serif;
    color: var(--white);
    position: relative;
  }
  .card {
    position: absolute;
    left: 320px;
    width: 560px;
    height: 320px;
    background: var(--card);
    border-radius: 18px;
    border-bottom: 4px solid var(--green);
    overflow: hidden;
  }
  .card-front { top: 100px; }
  .card-back { top: 480px; }

  .front-brand {
    position: absolute;
    inset: 0;
    display: flex;
    align-items: center;
    justify-content: center;
    gap: 18px;
  }
  .brand-square {
    width: 54px;
    height: 54px;
    background: var(--green);
    border-radius: 6px;
  }
  .brand-name {
    font-weight: 800;
    font-size: 34px;
    line-height: 1.05;
    letter-spacing: 1px;
    text-transform: uppercase;
    color: var(--white);
  }

  .back-badge {
    position: absolute;
    top: 26px;
    right: 30px;
    display: flex;
    align-items: center;
    gap: 12px;
  }
  .back-badge .brand-square {
    width: 110px;
    height: 110px;
    border-radius: 14px;
  }
  .back-badge .brand-name {
    font-size: 15px;
    text-align: right;
  }

  .divider {
    position: absolute;
    left: 34px;
    right: 34px;
    top: 196px;
    height: 1px;
    background: var(--green);
  }
  .person {
    position: absolute;
    left: 34px;
    top: 150px;
  }
  .person-name {
    font-weight: 700;
    font-size: 24px;
    color: var(--green);
  }
  .person-role {
    font-size: 13px;
    color: var(--white);
    margin-top: 10px;
  }
  .contact-list {
    position: absolute;
    left: 34px;
    top: 232px;
    list-style: none;
    font-size: 12.5px;
    color: var(--muted);
  }
  .contact-list li {
    display: flex;
    align-items: center;
    gap: 10px;
    margin-bottom: 7px;
  }
  .contact-list svg { width: 12px; height: 12px; flex: none; }
  .address {
    position: absolute;
    right: 34px;
    top: 216px;
    font-size: 12.5px;
    line-height: 1.5;
    text-align: right;
    color: var(--muted);
  }
</style>
</head>
<body>
  <section class="card card-front">
    <div class="front-brand">
      <span class="brand-square"></span>
      <span class="brand-name">Halvorsen<br>Construction</span>
    </div>
  </section>

  <section class="card card-back">
    <div class="back-badge">
      <span class="brand-name">Halvorsen<br>Construction</span>
      <span class="brand-square"></span>
    </div>

    <div class="person">
      <p class="person-name">Daniel Reyes</p>
    </div>
    <div class="divider"></div>
    <p class="person-role" style="position:absolute;left:34px;top:204px;margin:0;">Owner</p>

    <ul class="contact-list">
      <li>
        <svg viewBox="0 0 12 12"><path d="M2.5 1 L4.5 1 L5.2 3.4 L4 4.3 C4.6 5.7 6.3 7.4 7.7 8 L8.6 6.8 L11 7.5 L11 9.5 C11 10.3 10.3 11 9.5 11 C5 11 1 7 1 2.5 C1 1.7 1.7 1 2.5 1 Z" fill="var(--green)"/></svg>
        555-014-2290
      </li>
      <li>
        <svg viewBox="0 0 12 12"><rect x="1" y="2.5" width="10" height="7" rx="1" fill="var(--green)"/><path d="M1.5 3 L6 6.5 L10.5 3" stroke="var(--card)" stroke-width="1" fill="none"/></svg>
        info@halvorsenbuild.com
      </li>
      <li>
        <svg viewBox="0 0 12 12"><circle cx="6" cy="6" r="5" fill="none" stroke="var(--green)" stroke-width="1.2"/><path d="M1 6 H11 M6 1 C3.5 3.5 3.5 8.5 6 11 M6 1 C8.5 3.5 8.5 8.5 6 11" stroke="var(--green)" stroke-width="1" fill="none"/></svg>
        www.halvorsenbuild.com
      </li>
    </ul>

    <p class="address">42 Birch Hollow Ln<br>Millbrook, MO 63000</p>
  </section>
</body>
</html>
```